military training website velmotrail.com

I have a website that someone designed I am not happy with. It looks like the designer did not have the artistic ability to make a quality product. the power points are ideas that I had for the website. the business proposal was designed by someone else, and I like the style and font used, the website should reflect this document. The main part of the website should be informational with few pictures, maybe some background images behind or off to the side of the text. I would like to include a generic map with four locations marked, which, when you hover the cursor over them, show a picture of the actual location with an artistic effect or blurred so it doesn't look like a plivora atlas snip, and a picture that resembles what services are offered there, along with the text description, pictures can be found in the documents I attached, also can be stock images. this is outlined in the power points roughly.
Want to have the side menu of the major topics, or at the top, and scroll down a single page to find all of the information we have to offer

Target Market(s)

Special operations military

Industry/Entity Type

military

Coding

Coded - Design and coding required

Number of Pages Required

1 page

Other font styles liked:
• Agency FB

Colors
0054AA
0677BA
7BADD7
CADEEF
E8F1F8
00AB8E
00BBA5
67D7C9
C6EFE9
E9F9F6

Requirements
Must have
• interactive "map"
Nice to have
• professional design features to make it look like a professional website, not a beginner designer

```html
<!DOCTYPE html>
<html lang="en">
<head>
<meta charset="utf-8">
<title>Velmo Trail – Business Proposal</title>
<link rel="stylesheet" href="https://fonts.googleapis.com/css2?family=Oswald:wght@300;400&family=Merriweather:wght@400&family=Roboto:wght@300;400&display=swap">
<style>
:root{
  --ink-deep:#0f131b;
  --navy-mid:#222b3d;
  --text-light:#e9ecf1;
  --text-body:#b5bcc8;
  --text-muted:#9aa1ad;
  --line:#c9ced7;
  --frame:#f2f2f2;
  --brand-blue:#1c4f8c;
  --marker-gold:#e6a321;
  --marker-green:#3fb24a;
  --marker-teal:#1fb2b8;
  --caption-edge:#d8cf1c;
}
*{margin:0;padding:0;box-sizing:border-box}
html,body{width:1200px;height:3624px;overflow:hidden;background:var(--ink-deep)}
body{position:relative;font-family:"Roboto",Arial,sans-serif;color:var(--text-light)}
h1,h2,h3{font-weight:400}
.abs{position:absolute}
.display{font-family:"Oswald","Arial Narrow",sans-serif;font-weight:300;letter-spacing:0;text-align:center;color:#d9dce2;white-space:nowrap}
.serif-caps{font-family:"Merriweather",Georgia,serif;font-weight:400;text-transform:uppercase;letter-spacing:3px;color:var(--text-light);white-space:nowrap}

/* hero */
.hero{left:0;top:0;width:1200px;height:628px;background:linear-gradient(180deg,#7d8594 0%,#4a5264 22%,#2c3446 55%,#222a3b 100%)}
.site-header{left:0;top:0;width:1200px;height:89px;border-bottom:1px solid rgba(255,255,255,.55)}
.founder{left:73px;top:28px;font-family:"Oswald","Arial Narrow",sans-serif;font-weight:400;font-size:21px;letter-spacing:1px;color:#f3f3f3;white-space:nowrap}
.header-rule{top:0;width:1px;height:89px;background:rgba(255,255,255,.55)}
.brand{left:499px;top:0;width:201px;height:89px;display:flex;align-items:center;justify-content:center;gap:10px}
.brand-dot{width:18px;height:18px;border-radius:50%;background:var(--brand-blue);flex:none}
.brand-name{font-family:"Oswald","Arial Narrow",sans-serif;font-weight:400;font-size:24px;letter-spacing:2px;color:#f0f2f5;white-space:nowrap}
.compass{left:1082px;top:26px}
.hero-title{left:0;top:262px;width:1200px;font-size:96px;line-height:1.1;letter-spacing:2px}
.hero-sub{left:0;top:386px;width:1200px;display:flex;align-items:center;justify-content:center;gap:20px}
.hero-sub span{font-size:25px;letter-spacing:3px}
.hero-sub i{display:block;width:102px;height:1px;background:var(--line)}

/* nav strip */
.section-nav{left:0;top:628px;width:1200px;height:119px;background:var(--navy-mid);border-top:1px solid #3b4356;border-bottom:1px solid #3b4356}
.nav-item{top:0;width:298px;height:119px;background:linear-gradient(180deg,#2a2b30,#1b1c21);border-left:1px solid #44464d;display:flex;align-items:center;justify-content:center;text-align:center;font-family:"Merriweather",Georgia,serif;font-size:20px;line-height:28px;color:#eee;text-transform:uppercase}
.nav-arrow{top:36px}
.nav-gap{left:0;top:747px;width:1200px;height:73px;background:var(--navy-mid)}

/* section bands */
.band{left:0;width:1200px;height:345px}
.band-title{left:0;width:1200px;font-size:66px;line-height:1.1;letter-spacing:1px}
.band-sub{left:0;width:1200px;text-align:center;font-size:21px}
.band-exec{top:820px;background:linear-gradient(180deg,#343b4a,#2a3142 60%,#262d3c)}
.overview{left:0;top:1165px;width:1200px;height:823px;background:linear-gradient(160deg,#1b2333,#1e2637 50%,#182030)}
.photo-frame{left:75px;top:1273px;width:460px;height:657px;border:4px solid var(--frame);background:linear-gradient(180deg,#5a606a,#474c55 50%,#3e434b)}
.overview-heading{left:611px;top:1428px;width:514px;text-align:center;font-size:24px;letter-spacing:2px}
.overview-text{left:611px;top:1484px;width:514px;font-size:19px;line-height:30px;color:var(--text-body);text-align:justify;font-weight:300;hyphens:auto}
.band-company{top:1988px;background:linear-gradient(180deg,#262626,#222,#1c1c1c)}

/* dark section */
.details{left:0;top:2333px;width:1200px;height:1291px;background:linear-gradient(180deg,#151515,#1a1b1c 40%,#131313)}
.col-heading{font-size:24px;letter-spacing:2px}
.col-text{font-size:19px;line-height:30px;color:var(--text-muted);font-weight:300}
.mission-heading{left:75px;top:2494px}
.mission-text{left:75px;top:2548px;width:536px;text-align:justify}
.members-heading{left:687px;top:2494px}
.members-text{left:687px;top:2548px;width:438px}
.location-heading{left:0;top:2842px;width:1200px;text-align:center;font-size:25px;letter-spacing:2px}
.map-frame{left:75px;top:2912px;width:1050px;height:581px;border:4px solid var(--frame);background:linear-gradient(160deg,#3a4a3c 0%,#34452f 50%,#2e3d2c 100%);overflow:hidden}
.region-box{position:absolute;border:2px solid}
.region-green{left:367px;top:148px;width:162px;height:95px;background:rgba(100,200,80,.45);border-color:#8de07a}
.region-teal{left:598px;top:14px;width:214px;height:75px;background:rgba(70,190,210,.4);border-color:#7fd8e8}
.marker{position:absolute}
.map-caption{position:absolute;left:180px;top:456px;width:681px;height:67px;border:2px solid var(--caption-edge);background:rgba(40,45,40,.55);display:flex;align-items:center;justify-content:center;font-size:18px;color:#f2f2f2}
</style>
</head>
<body>

<section class="abs hero" role="img" aria-label="Tiltrotor aircraft on a carrier deck with soldiers walking toward it"></section>

<header class="abs site-header">
  <div class="abs founder">FOUNDER: DORIAN VASK</div>
  <div class="abs header-rule" style="left:498px"></div>
  <div class="abs header-rule" style="left:700px"></div>
  <div class="abs brand">
    <div class="brand-dot"></div>
    <div class="brand-name">VELMO TRAIL</div>
  </div>
  <svg class="abs compass" width="38" height="38" viewBox="0 0 38 38" aria-hidden="true">
    <circle cx="19" cy="19" r="17" fill="rgba(255,255,255,.15)" stroke="#ddd" stroke-width="1.5"/>
    <path d="M19 6 L22 19 L19 32 L16 19Z M6 19 L19 16 L32 19 L19 22Z" fill="#eee"/>
  </svg>
</header>

<h1 class="abs display hero-title">VELMO TRAIL</h1>
<div class="abs hero-sub serif-caps"><i></i><span>Business Proposal</span><i></i></div>

<nav class="abs section-nav">
  <svg class="abs nav-arrow" style="left:78px" width="44" height="48" viewBox="0 0 44 48" aria-hidden="true">
    <path d="M24 6 L8 24 L24 42" fill="none" stroke="#fff" stroke-width="5"/>
    <path d="M38 6 L22 24 L38 42" fill="none" stroke="rgba(255,255,255,.3)" stroke-width="4"/>
  </svg>
  <div class="abs nav-item" style="left:152px">Executive<br>Summary</div>
  <div class="abs nav-item" style="left:450px">Company<br>Description</div>
  <div class="abs nav-item" style="left:748px">Market<br>Research</div>
  <svg class="abs nav-arrow" style="left:1064px" width="56" height="48" viewBox="0 0 56 48" aria-hidden="true">
    <path d="M6 6 L22 24 L6 42" fill="none" stroke="rgba(255,255,255,.3)" stroke-width="4"/>
    <path d="M28 6 L44 24 L28 42" fill="none" stroke="#fff" stroke-width="5"/>
  </svg>
</nav>
<div class="abs nav-gap"></div>

<section class="abs band band-exec" role="img" aria-label="Soldiers advancing across a field with rifles raised"></section>
<h2 class="abs display band-title" style="top:934px">EXECUTIVE SUMMARY</h2>
<p class="abs serif-caps band-sub" style="top:1022px">Shoot, Move, Communicate</p>

<section class="abs overview" role="img" aria-label="Faint camouflage pattern background"></section>
<div class="abs photo-frame" role="img" aria-label="Military helicopter landing on a rocky field"></div>
<h3 class="abs serif-caps overview-heading">Overview</h3>
<p class="abs overview-text" lang="en">Velmo Trail will be the only facility in the region to offer professional firearms instruction by industry leading professionals with special operations experience in a state-of-the - art facility. We will be equipped with shooting ranges, mock villages for full mission planning scenarios, lodging, and relaxation facilities. We offer a place for the world’s highest trained Special Operators to conduct exercises while remaining open to the public for recreational use.</p>

<section class="abs band band-company" role="img" aria-label="Silhouetted operators in low light"></section>
<h2 class="abs display band-title" style="top:2096px">COMPANY DESCRIPTION</h2>
<p class="abs serif-caps band-sub" style="top:2185px">Whatever It Takes</p>

<section class="abs details" role="img" aria-label="Dark textured background"></section>
<h3 class="abs serif-caps col-heading mission-heading">Mission Statement</h3>
<p class="abs col-text mission-text">Velmo Trail will utilize the experience gained from spending years in US Special Operations to provide professional instruction and world class training facilities that will be sought after by both the top military personnel stationed in Europe as well as civilians and tourists.</p>
<h3 class="abs serif-caps col-heading members-heading">Principal Members</h3>
<p class="abs col-text members-text">Dorian Vask- Owner/Instructor<br>Tarmo Leevik- Owner</p>

<h3 class="abs serif-caps location-heading">Location</h3>
<div class="abs map-frame" role="img" aria-label="Satellite map of the region with three candidate property areas">
  <div class="region-box region-green"></div>
  <div class="region-box region-teal"></div>
  <svg class="marker" style="left:196px;top:126px" width="80" height="110" viewBox="0 0 80 110" aria-hidden="true">
    <circle cx="40" cy="38" r="34" fill="rgba(255,255,255,.15)" stroke="#fff" stroke-width="3"/>
    <circle cx="40" cy="38" r="20" fill="var(--marker-gold)"/>
    <path d="M22 92 L40 78 L58 92" fill="none" stroke="#fff" stroke-width="6"/>
    <path d="M22 106 L40 92 L58 106" fill="none" stroke="rgba(255,255,255,.4)" stroke-width="6"/>
  </svg>
  <svg class="marker" style="left:409px;top:158px" width="80" height="110" viewBox="0 0 80 110" aria-hidden="true">
    <circle cx="40" cy="38" r="34" fill="rgba(255,255,255,.15)" stroke="#fff" stroke-width="3"/>
    <circle cx="40" cy="38" r="20" fill="var(--marker-green)"/>
    <path d="M22 92 L40 78 L58 92" fill="none" stroke="#fff" stroke-width="6"/>
    <path d="M22 106 L40 92 L58 106" fill="none" stroke="rgba(255,255,255,.4)" stroke-width="6"/>
  </svg>
  <svg class="marker" style="left:656px;top:6px" width="80" height="110" viewBox="0 0 80 110" aria-hidden="true">
    <circle cx="40" cy="38" r="34" fill="rgba(255,255,255,.15)" stroke="#fff" stroke-width="3"/>
    <circle cx="40" cy="38" r="20" fill="var(--marker-teal)"/>
    <path d="M22 92 L40 78 L58 92" fill="none" stroke="#fff" stroke-width="6"/>
    <path d="M22 106 L40 92 L58 106" fill="none" stroke="rgba(255,255,255,.4)" stroke-width="6"/>
  </svg>
  <div class="map-caption">We have identified suitable properties for sale in three regions of Estonia.</div>
</div>

</body>
</html>
```